Business Card for premium dental clinic

We are a premium dental clinic based in Brasov, Romania with more than 15 year on the market, providing quality dental treatment made by a team of more specialized dentists, working with modern equipment as a solution to beautiful and healthy teeth.

Our current logo for the clinic use 2 square with colors black and gold - dr Ternisu - studio, using family fonts Bodoni, Myriad Pro and Segoe Print.
Depending on the printing we used some gold CMYK background or gold foil picture background or a gold gradient.
We want a business card:
- eye catching business card
- distinguished business card
- premium design
- to keep the color scheme of black and gold
- to attract the customers to spent time reading the information
- modern concept

```html
<!DOCTYPE html>
<html lang="en">
<head>
<meta charset="utf-8">
<title>dr Ternisu studio – business card</title>
<link rel="stylesheet" href="https://fonts.googleapis.com/css2?family=Roboto+Condensed:wght@400&family=Source+Sans+3:wght@400&display=swap">
<style>
  :root {
    --bg: #d6d6d6;
    --card: #0b0b0b;
    --white: #ffffff;
    --ink: #1a1a1a;
    --gold-light: #f4d46a;
    --gold: #e0ad2a;
    --gold-deep: #b8801a;
  }
  * { margin: 0; padding: 0; box-sizing: border-box; }
  html, body {
    width: 1200px; height: 1006px; overflow: hidden;
    background: var(--bg);
  }
  .card {
    position: absolute; left: 100px; top: 225px;
    width: 1000px; height: 556px;
    background: var(--card);
    box-shadow: 0 18px 40px rgba(0,0,0,.35);
  }
  .frame {
    position: absolute; left: 80px; top: 50px;
    width: 860px; height: 375px;
    border: 3px solid var(--white);
    overflow: hidden;
  }
  .gold-panel {
    position: absolute; left: 0; top: 0;
    width: 390px; height: 100%;
    background: radial-gradient(ellipse at 40% 40%, var(--gold-light) 0%, var(--gold) 55%, var(--gold-deep) 100%);
  }
  .name-box {
    position: absolute; left: 70px; top: 168px;
    width: 330px; height: 112px;
    background: var(--white);
    display: flex; align-items: center; padding-left: 40px;
  }
  .name {
    font-family: "Roboto Condensed", sans-serif;
    font-weight: 400; font-size: 66px; color: var(--ink);
    letter-spacing: -1px; white-space: nowrap;
  }
  .studio {
    position: absolute; left: 470px; top: 120px;
    font-family: "Roboto Condensed", sans-serif;
    font-weight: 400; font-size: 72px; color: var(--white);
  }
  .tagline {
    position: absolute; right: 24px; bottom: 18px;
    font-family: "Roboto Condensed", sans-serif;
    font-size: 46px; color: var(--white);
  }
  .contact {
    position: absolute; top: 445px;
    font-family: "Source Sans 3", sans-serif;
    font-size: 22px; line-height: 32px; color: var(--white);
  }
  .address { left: 90px; }
  .phones { left: 460px; }
  .online { left: 700px; }
  .contact li { list-style: none; display: flex; align-items: center; gap: 8px; }
  .icon { width: 18px; height: 18px; flex: none; }
</style>
</head>
<body>
  <div class="card">
    <div class="frame">
      <div class="gold-panel" role="img" aria-label="Crumpled gold foil texture"></div>
      <div class="name-box"><span class="name">dr. ternisu</span></div>
      <div class="studio">studio</div>
      <div class="tagline">dental clinic</div>
    </div>

    <div class="contact address">
      <p>strada Lunga nr 24</p>
      <p>Brasov, Romania 500058</p>
    </div>

    <ul class="contact phones">
      <li>
        <svg class="icon" viewBox="0 0 18 18"><rect x="5" y="1" width="8" height="16" rx="1.5" fill="none" stroke="var(--gold)" stroke-width="1.6"/><line x1="8" y1="14.5" x2="10" y2="14.5" stroke="var(--gold)" stroke-width="1.6"/></svg>
        +40 700 318 552
      </li>
      <li>
        <svg class="icon" viewBox="0 0 18 18"><path d="M3 2 L6.5 1.5 L8 5.5 L6 7 C7 9.5 8.5 11 11 12 L12.5 10 L16.5 11.5 L16 15 C9 15.5 2.5 9 3 2 Z" fill="var(--gold)"/></svg>
        +40 268 410 925
      </li>
    </ul>

    <ul class="contact online">
      <li>
        <svg class="icon" viewBox="0 0 18 18"><rect x="1.5" y="3.5" width="15" height="11" fill="none" stroke="var(--gold)" stroke-width="1.6"/><path d="M1.5 3.5 L9 10 L16.5 3.5" fill="none" stroke="var(--gold)" stroke-width="1.6"/></svg>
        info@drternisu.ro
      </li>
      <li>
        <svg class="icon" viewBox="0 0 18 18"><circle cx="9" cy="9" r="7.5" fill="none" stroke="var(--gold)" stroke-width="1.5"/><ellipse cx="9" cy="9" rx="3.2" ry="7.5" fill="none" stroke="var(--gold)" stroke-width="1.3"/><line x1="1.5" y1="9" x2="16.5" y2="9" stroke="var(--gold)" stroke-width="1.3"/></svg>
        www.drternisu.ro
      </li>
    </ul>
  </div>
</body>
</html>
```